BrindleStaffing Business Card Design

We are a staffing company finding positions for dedicated nurses and physicians.

Target Market(s)

Business Professionals

Industry/Entity Type

Staffing

Contact Information for Business Card

Gordon Pratley
Chairman
417 39th Avenue South
SAINT PETERSBURG FL 33712
813-555-4172 Mobile
813-555-8036 Fax
gpratley@brindlestaffing.com
www.brindlestaffing.com

Font styles to use
Sans Serif

Colors
fbee3e
f04a50
f37122

Requirements
Must have
• Logo Attached, see colors below. We'd like to see Yellow, Orange and Red.

```html
<!DOCTYPE html>
<html lang="en">
<head>
<meta charset="utf-8">
<title>BrindleStaffing Business Card</title>
<link rel="stylesheet" href="https://fonts.googleapis.com/css2?family=Open+Sans:wght@400;600;700&display=swap">
<style>
  :root {
    --backdrop: #3a3a3c;
    --card: #0d0d0e;
    --card-edge: #1c1c1e;
    --brand-yellow: #fbee3e;
    --brand-orange: #f37122;
    --brand-red: #f04a50;
    --text-light: #f2f2f2;
    --text-muted: #bdbdbd;
  }
  * { margin: 0; padding: 0; box-sizing: border-box; }
  html, body {
    width: 1200px; height: 717px; overflow: hidden;
    background: var(--backdrop);
    font-family: "Open Sans", sans-serif;
  }
  .canvas { position: relative; width: 1200px; height: 717px; }
  .card {
    position: absolute; top: 204px;
    width: 540px; height: 309px;
    background: linear-gradient(135deg, var(--card-edge) 0%, var(--card) 60%);
    box-shadow: 0 10px 30px rgba(0,0,0,.45);
  }
  .card--front { left: 40px; }
  .card--back { left: 620px; }

  .wordmark {
    position: absolute;
    font-weight: 700; color: var(--brand-orange);
    letter-spacing: -0.5px; white-space: nowrap; line-height: 1;
  }
  .card--front .wordmark {
    left: 0; right: 0; top: 130px; text-align: center; font-size: 44px;
  }
  .card--back .wordmark { right: 34px; top: 60px; font-size: 34px; }

  .holder {
    position: absolute; right: 110px; top: 114px; text-align: left;
  }
  .holder-name {
    font-size: 21px; line-height: 1.2; color: var(--brand-red); font-weight: 400;
  }
  .holder-title {
    font-size: 12px; line-height: 1.3; color: var(--text-muted);
    letter-spacing: 1.5px; text-transform: uppercase;
  }

  .contact-list {
    position: absolute; list-style: none;
    font-size: 13px; color: var(--text-light); line-height: 1.35;
  }
  .contact-list--left { left: 34px; top: 178px; }
  .contact-list--right { left: 296px; top: 218px; }
  .contact-list li { display: flex; align-items: flex-start; gap: 8px; margin-bottom: 3px; }
  .contact-label { color: var(--text-muted); font-size: 11px; margin-left: 4px; }
  .contact-icon {
    flex: 0 0 13px; width: 13px; height: 13px; margin-top: 2px;
    background: var(--brand-orange); border-radius: 2px;
    display: flex; align-items: center; justify-content: center;
  }
  .contact-icon svg { width: 9px; height: 9px; }
  .divider {
    position: absolute; left: 268px; top: 206px;
    width: 2px; height: 58px; background: var(--brand-yellow);
  }
</style>
</head>
<body>
<main class="canvas">
  <section class="card card--front" aria-label="Card front">
    <div class="wordmark">BrindleStaffing</div>
  </section>

  <section class="card card--back" aria-label="Card back">
    <div class="wordmark">BrindleStaffing</div>
    <div class="holder">
      <div class="holder-name">Gordon Pratley</div>
      <div class="holder-title">Chairman</div>
    </div>

    <ul class="contact-list contact-list--left">
      <li>
        <span class="contact-icon"><svg viewBox="0 0 10 10"><path d="M2 1h2l1 2-1 1c.5 1 1 1.5 2 2l1-1 2 1v2c-4 1-9-4-8-8z" fill="#fff"/></svg></span>
        <span>813-555-4172<span class="contact-label">Mobile</span></span>
      </li>
      <li>
        <span class="contact-icon"><svg viewBox="0 0 10 10"><rect x="2.5" y="1" width="5" height="3" fill="none" stroke="#fff"/><rect x="1" y="4" width="8" height="4.5" fill="#fff"/></svg></span>
        <span>813-555-8036<span class="contact-label">Fax</span></span>
      </li>
      <li>
        <span class="contact-icon"><svg viewBox="0 0 10 10"><rect x="1" y="2" width="8" height="6" fill="none" stroke="#fff"/><path d="M1 2l4 3.5L9 2" fill="none" stroke="#fff"/></svg></span>
        <span>gpratley@brindlestaffing.com</span>
      </li>
    </ul>

    <div class="divider"></div>

    <ul class="contact-list contact-list--right">
      <li>
        <span class="contact-icon"><svg viewBox="0 0 10 10"><circle cx="5" cy="5" r="3.8" fill="none" stroke="#fff"/><path d="M1.2 5h7.6M5 1.2c-2 2.5-2 5 0 7.6M5 1.2c2 2.5 2 5 0 7.6" fill="none" stroke="#fff" stroke-width=".8"/></svg></span>
        <span>www.brindlestaffing.com</span>
      </li>
      <li>
        <span class="contact-icon"><svg viewBox="0 0 10 10"><path d="M5 9.5C2.5 6.5 2 5.2 2 4a3 3 0 016 0c0 1.2-.5 2.5-3 5.5z" fill="#fff"/><circle cx="5" cy="4" r="1" fill="#f37122"/></svg></span>
        <span>417 39th Avenue South<br>SAINT PETERSBURG FL 33712</span>
      </li>
    </ul>
  </section>
</main>
</body>
</html>
```